High value cover design for an A4 ideation pad.

The product is NOT A BOOK.

It's an A4 ideation pad for professionals, designers and creators who handwrite their ideas. Visualise creators like Milo Varnet, Owen Plaskit and Gregor Lunwick in your mind's eye.

I'm looking for a cover design for the ideation pad. Both front and back.

It should look, feel and convey the following.

--> A handcrafted product experience

--> High value & Elegance

--> Inspiration

Mandatory --> See Uploaded Files --> Files 1, 5 & 6

Target Market(s)

- Designers

-Creative Professionals

- Entrepreneurs

who handwrite their ideas. Visualise creators like Milo Varnet, Owen Plaskit and Gregor Lunwick in your mind's eye.

Industry/Entity Type

Stationary

Font styles to use
Script
Other font styles liked:
• Calligraphy

Colors
fbed22

Requirements
Must have
• Title text - Quiet Kettle Notes

-Text in gold on brown leather background to convey high value for the front cover.

--> High value & Elegance

--> Inspiration

--> Should compel the customers to pick up and own the idea pad
Nice to have
• That's my take but other ideas are welcome
Should not have
• Must not convey

- low value

```html
<!DOCTYPE html>
<html lang="en">
<head>
<meta charset="utf-8">
<title>Quiet Kettle Notes — Ideation Pad Covers</title>
<link rel="stylesheet" href="https://fonts.googleapis.com/css2?family=Pinyon+Script&display=swap">
<style>
  :root {
    --backdrop: #f4f1ec;
    --leather-light: #a8683f;
    --leather-mid: #8a4f2c;
    --leather-dark: #5e3119;
    --gold: #e0b24a;
    --coil: #b89a6a;
  }
  html, body {
    margin: 0;
    padding: 0;
    width: 1200px;
    height: 878px;
    overflow: hidden;
    background: var(--backdrop);
  }
  .spread {
    position: relative;
    width: 1200px;
    height: 878px;
  }
  .pad {
    position: absolute;
    top: 82px;
    width: 446px;
    height: 624px;
  }
  .pad--front { left: 81px; }
  .pad--back { left: 677px; }
  .pad__binding {
    position: absolute;
    top: -8px;
    left: 10px;
    width: 426px;
    height: 16px;
  }
  .pad__cover {
    position: absolute;
    inset: 0;
    background: radial-gradient(ellipse at 45% 35%, var(--leather-light) 0%, var(--leather-mid) 55%, var(--leather-dark) 100%);
    box-shadow: 0 2px 6px rgba(60, 40, 20, 0.25);
  }
  .pad--back .pad__cover {
    background: radial-gradient(ellipse at 50% 30%, var(--leather-light) 0%, var(--leather-mid) 50%, var(--leather-dark) 100%);
  }
  .title {
    position: absolute;
    margin: 0;
    font-family: "Pinyon Script", cursive;
    font-weight: 400;
    color: var(--gold);
    text-align: center;
    line-height: 1.2;
    white-space: nowrap;
  }
  .title--front {
    left: 0;
    width: 446px;
    top: 282px;
    font-size: 36px;
  }
  .title--back {
    left: 123px;
    width: 200px;
    top: 532px;
    font-size: 20px;
  }
</style>
</head>
<body>
<main class="spread">
  <section class="pad pad--front" aria-label="Front cover">
    <div class="pad__cover" role="img" aria-label="Brown leather texture cover"></div>
    <svg class="pad__binding" viewBox="0 0 426 16" aria-hidden="true">
      <path fill="none" stroke="var(--coil)" stroke-width="1.6" d="M4 12V3M12 12V3M20 12V3M28 12V3M36 12V3M44 12V3M52 12V3M60 12V3M68 12V3M76 12V3M84 12V3M92 12V3M100 12V3M108 12V3M116 12V3M124 12V3M132 12V3M140 12V3M148 12V3M156 12V3M164 12V3M172 12V3M180 12V3M188 12V3M196 12V3M204 12V3M212 12V3M220 12V3M228 12V3M236 12V3M244 12V3M252 12V3M260 12V3M268 12V3M276 12V3M284 12V3M292 12V3M300 12V3M308 12V3M316 12V3M324 12V3M332 12V3M340 12V3M348 12V3M356 12V3M364 12V3M372 12V3M380 12V3M388 12V3M396 12V3M404 12V3M412 12V3M420 12V3"/>
    </svg>
    <h1 class="title title--front">Quiet Kettle Notes</h1>
  </section>

  <section class="pad pad--back" aria-label="Back cover">
    <div class="pad__cover" role="img" aria-label="Brown leather texture cover"></div>
    <svg class="pad__binding" viewBox="0 0 426 16" aria-hidden="true">
      <path fill="none" stroke="var(--coil)" stroke-width="1.6" d="M4 12V3M12 12V3M20 12V3M28 12V3M36 12V3M44 12V3M52 12V3M60 12V3M68 12V3M76 12V3M84 12V3M92 12V3M100 12V3M108 12V3M116 12V3M124 12V3M132 12V3M140 12V3M148 12V3M156 12V3M164 12V3M172 12V3M180 12V3M188 12V3M196 12V3M204 12V3M212 12V3M220 12V3M228 12V3M236 12V3M244 12V3M252 12V3M260 12V3M268 12V3M276 12V3M284 12V3M292 12V3M300 12V3M308 12V3M316 12V3M324 12V3M332 12V3M340 12V3M348 12V3M356 12V3M364 12V3M372 12V3M380 12V3M388 12V3M396 12V3M404 12V3M412 12V3M420 12V3"/>
    </svg>
    <p class="title title--back">Quiet Kettle Notes</p>
  </section>
</main>
</body>
</html>
```